The Visual Personality of Miss Cobbler Food Trailer

Something that stands out with color and our logo. This is a food trailer that attends several events in the spring and summer. We are known for being one of the best Gumbo producers in mid Michigan. We have been responsible for connecting different communities and cultures together and we are strong supporters of our veterans since this is a veteran owned business. All of our vegetables are fresh and locally purchased. These recipes are originally from New Orleans Louisiana. Our website is Misscobbler.net. This will be used for an 8" x 11" poster. Leave a box or area that states "WHERE WE WILL BE:" so that we can add the location of the event that we are attending.

Target Market(s)

We do cuisine that is recognized in the southern states of the USA. but live in the northern part of the USA. We are providing a menu of different southern recipes so they do not have to go all the way down south for get..

Industry/Entity Type

Food/Restaurant Industry

Font styles to use
Serif
Decorative

Colors
0094D4
00A9DD
6FCCEA
C7EBF8
E9F6FB
59FF00
82FF00
B8FF75
E3FFCB
F4FFEA
FFF300
FFF600
FEFA6F
FFFEC7
FFFEE8
EE7325
F08F49
F5BC92
FAE3D3
FDF4ED
EB3D1F
EC4F4E
F09395
F8D3D4
FCEDEE
A7469A
B969AE
D3A5CF
EDDBEB
F8F0F9

Requirements
Must have
• Our logo, which is "Miss Cobbler", "Homemade Deliciousness". We need an area on the poster where we can manually add the location of the event we will be attending because it changes weekly. location
Nice to have
• Bold colors and logo

```html
<!DOCTYPE html>
<html lang="en">
<head>
<meta charset="utf-8">
<title>Miss Cobbler Food Trailer Poster</title>
<link rel="stylesheet" href="https://fonts.googleapis.com/css2?family=Bree+Serif&family=Fraunces:opsz,wght@9..144,400&display=swap">
<style>
  :root {
    --sun-yellow: #fde64b;
    --trailer-red: #dc1a20;
    --cream: #fffbe8;
    --address-pink: #ebc8c0;
    --strip-white: #f7f5f2;
    --ink: #2a2020;
  }
  html, body {
    margin: 0;
    padding: 0;
    overflow: hidden;
    background: #ffffff;
  }
  .poster {
    position: relative;
    width: 848px;
    height: 1200px;
    overflow: hidden;
    background: var(--sun-yellow);
    font-family: "Bree Serif", Georgia, serif;
  }
  .hero-photo {
    position: absolute;
    left: 0;
    top: 0;
    width: 848px;
    height: 575px;
    background:
      radial-gradient(ellipse 30% 22% at 48% 48%, #d8202a 0%, rgba(216,32,42,0) 100%),
      radial-gradient(ellipse 22% 18% at 25% 78%, #d42a25 0%, rgba(212,42,37,0) 100%),
      radial-gradient(ellipse 55% 30% at 60% 25%, #d98d4c 0%, rgba(217,141,76,0) 100%),
      linear-gradient(160deg, #e9e4dc 0%, #d89a5e 35%, #c9b79a 60%, #b58a55 85%, #8d8c92 100%);
  }
  .hero-strip {
    position: absolute;
    left: 0;
    top: 575px;
    width: 848px;
    height: 15px;
    background: var(--strip-white);
  }
  .brand-badge {
    position: absolute;
    left: -42px;
    top: -29px;
    width: 286px;
    height: 286px;
    border-radius: 50%;
    background: var(--sun-yellow);
  }
  .brand-name {
    position: absolute;
    left: 0;
    top: 80px;
    width: 210px;
    text-align: center;
    font-family: "Bree Serif", Georgia, serif;
    font-size: 30px;
    line-height: 36px;
    color: var(--trailer-red);
  }
  .headline {
    position: absolute;
    left: 30px;
    top: 612px;
    margin: 0;
    font-family: "Fraunces", Georgia, serif;
    font-weight: 400;
    font-size: 58px;
    line-height: 66px;
    color: var(--trailer-red);
  }
  .about {
    position: absolute;
    left: 30px;
    top: 770px;
    width: 390px;
    margin: 0;
    font-size: 18.5px;
    line-height: 27.5px;
    color: var(--ink);
    text-align: justify;
  }
  .location-panel {
    position: absolute;
    left: 0;
    top: 950px;
    width: 419px;
    height: 250px;
    background: var(--trailer-red);
    border-top-right-radius: 22px;
  }
  .location-title {
    position: absolute;
    left: 28px;
    top: 38px;
    margin: 0;
    font-size: 30px;
    line-height: 36px;
    font-weight: 400;
    color: #ffffff;
  }
  .address-box {
    position: absolute;
    left: 28px;
    top: 88px;
    width: 365px;
    height: 135px;
    background: var(--cream);
    display: flex;
    align-items: center;
    justify-content: center;
    font-size: 19px;
    letter-spacing: 2px;
    color: var(--address-pink);
  }
  .dish-photo {
    position: absolute;
    border: 10px solid var(--trailer-red);
    box-sizing: border-box;
  }
  .dish-photo--gumbo {
    left: 470px;
    top: 612px;
    width: 330px;
    height: 228px;
    transform: rotate(4deg);
    background:
      radial-gradient(ellipse 45% 42% at 45% 45%, #c4552c 0%, #b8472a 50%, rgba(184,71,42,0) 75%),
      linear-gradient(135deg, #e6e1dc 0%, #d9cfc7 50%, #bdb3ab 100%);
  }
  .dish-photo--poboy {
    left: 519px;
    top: 867px;
    width: 228px;
    height: 148px;
    transform: rotate(-4deg);
    background:
      radial-gradient(ellipse 40% 20% at 45% 62%, #6d7b3c 0%, rgba(109,123,60,0) 100%),
      linear-gradient(170deg, #c9874a 0%, #e0a567 35%, #b36a3a 60%, #d8b68d 80%, #7a6a40 100%);
  }
  .hours {
    position: absolute;
    left: 440px;
    top: 1126px;
    width: 386px;
    margin: 0;
    text-align: center;
    font-size: 22px;
    line-height: 30px;
    color: var(--trailer-red);
  }
</style>
</head>
<body>
  <main class="poster">
    <div class="hero-photo" role="img" aria-label="Close-up photo of a fried po'boy sandwich with tomato slices, shredded lettuce and remoulade on French bread"></div>
    <div class="hero-strip"></div>

    <div class="brand-badge">
      <div class="brand-name" style="left:42px; top:110px;">Miss Cobbler</div>
    </div>

    <h1 class="headline">Homemade<br>Deliciousness</h1>

    <p class="about">We prepare and serve amazing high quality, delicious southern food at an affordable price. We want to provide our customers with the most authentic Louisiana experience outside of Louisiana.</p>

    <div class="dish-photo dish-photo--gumbo" role="img" aria-label="Photo of a bowl of gumbo with tomatoes, peppers and rice"></div>
    <div class="dish-photo dish-photo--poboy" role="img" aria-label="Photo of a halved po'boy sandwich with fries"></div>

    <section class="location-panel">
      <h2 class="location-title">where we will be</h2>
      <div class="address-box">YOUR ADDRESS HERE</div>
    </section>

    <p class="hours">Monday, Friday, Saturday<br>11:00 am EST - 3 pm EST</p>
  </main>
</body>
</html>
```